Harbor Law Stationary - Law Firm

I am looking for a designer who can help me design letterhead and envelopes consistent with our new business cards. Feel free to reach out to me directly at ned@harborlawgroup.example. Thank you!! Visit harborlawgroup.example to see our site and the attached files for creative assets.

Target Market(s)

Anyone needing a lawyer

Font styles to use
Other font styles liked:
• Adobe Caslon Pro

Requirements
Must have
• Adobe Caslon Pro font
Full color
Nice to have
• My photo on front along with 2/3 face of camo - see mock up for example of what I have in mind.

American colors - similar to the ones found on my website and gold.

```html
<!DOCTYPE html>
<html lang="en">
<head>
<meta charset="utf-8">
<title>Harbor Law Stationery</title>
<link rel="stylesheet" href="https://fonts.googleapis.com/css2?family=Libre+Caslon+Text:wght@400;700&family=Montserrat:wght@300;400&family=Mrs+Saint+Delafield&display=swap">
<style>
  :root {
    --navy: #0d2647;
    --gold: #a8925a;
    --paper: #ffffff;
    --ink: #3a3a3a;
    --muted: #9a9a9a;
    --backdrop: #b6cee6;
    --serif: "Libre Caslon Text", "Times New Roman", serif;
    --sans: "Montserrat", Arial, sans-serif;
  }
  * { margin: 0; padding: 0; box-sizing: border-box; }
  html, body { width: 1200px; height: 1200px; overflow: hidden; }
  body { background: var(--backdrop); position: relative; font-family: var(--sans); }

  .brand-name {
    font-family: var(--serif); font-weight: 700; color: var(--gold);
    text-transform: uppercase; letter-spacing: 0.5px; white-space: nowrap;
  }

  /* Letterhead */
  .letterhead { position: absolute; left: 77px; top: 265px; width: 460px; height: 650px; background: var(--paper); overflow: hidden; }
  .letterhead-band { position: absolute; left: 0; top: 0; width: 100%; height: 74px; background: var(--navy); }
  .letterhead-band .brand-name { position: absolute; left: 53px; top: 28px; font-size: 15px; }
  .contact-block {
    position: absolute; right: 12px; top: 12px; height: 52px;
    border-left: 1px solid rgba(255,255,255,0.5); padding-left: 8px;
    font-family: var(--serif); font-weight: 400; font-size: 6.6px; color: #fff;
    line-height: 9.5px; white-space: nowrap;
  }
  .contact-line { display: flex; align-items: center; gap: 3px; }
  .contact-line svg { width: 6px; height: 6px; flex: none; }
  .contact-address { margin-top: 5px; }

  .recipient { position: absolute; left: 47px; top: 145px; }
  .recipient-label { font-size: 8px; letter-spacing: 1px; color: var(--ink); }
  .recipient-name { font-size: 7px; color: var(--gold); margin-top: 3px; }
  .recipient-detail { font-size: 5.2px; color: var(--muted); line-height: 10px; margin-top: 2px; }
  .letter-date { position: absolute; right: 46px; top: 147px; font-size: 6px; color: var(--ink); }

  .letter-body { position: absolute; left: 47px; top: 233px; width: 367px; font-size: 5.7px; line-height: 8.1px; color: var(--muted); text-align: justify; font-weight: 300; }
  .letter-body p { margin-bottom: 8px; }

  .signature { position: absolute; left: 47px; top: 452px; font-family: "Mrs Saint Delafield", cursive; font-size: 24px; color: var(--ink); white-space: nowrap; }
  .signer-name { position: absolute; left: 46px; top: 484px; font-size: 7.4px; color: var(--ink); }
  .signer-title { position: absolute; left: 46px; top: 495px; font-size: 5.2px; color: var(--muted); }

  /* Envelope front */
  .envelope-front { position: absolute; left: 574px; top: 310px; width: 549px; height: 240px; background: var(--paper); }
  .envelope-front-band { position: absolute; left: 0; top: 0; width: 100%; height: 77px; background: var(--navy); }
  .envelope-front-band .brand-name { position: absolute; left: 48px; top: 28px; font-size: 15px; }
  .return-address { position: absolute; left: 48px; top: 50px; font-family: var(--serif); font-weight: 400; font-size: 6.8px; line-height: 9.6px; color: #fff; white-space: nowrap; }

  /* Envelope back */
  .envelope-back { position: absolute; left: 574px; top: 626px; width: 549px; height: 238px; background: var(--paper); }
  .envelope-flap { position: absolute; left: 0; top: 0; width: 549px; height: 66px; }
  .envelope-flap svg { position: absolute; left: 0; top: 0; }
  .envelope-flap .brand-name { position: absolute; left: 0; width: 100%; top: 25px; text-align: center; font-size: 14px; }
</style>
</head>
<body>

<section class="letterhead">
  <header class="letterhead-band">
    <div class="brand-name">Harbor Law</div>
    <div class="contact-block">
      <div class="contact-line">
        <svg viewBox="0 0 10 10"><path d="M2 1 L4 1 L5 3.5 L3.8 4.5 Q5 6.5 6 7 L7 5.8 L9 7 L9 9 Q4 9.5 1 2 Z" fill="var(--gold)"/></svg>
        <span>555 014 2290</span>
      </div>
      <div class="contact-line">
        <svg viewBox="0 0 10 10"><rect x="0.5" y="2" width="9" height="6" fill="var(--gold)"/><path d="M0.5 2 L5 5.5 L9.5 2" stroke="var(--navy)" stroke-width="1" fill="none"/></svg>
        <span>clara@harborlawgroup.example</span>
      </div>
      <div class="contact-line">
        <svg viewBox="0 0 10 10"><circle cx="5" cy="5" r="4.2" fill="none" stroke="var(--gold)" stroke-width="1.2"/><path d="M1 5 H9 M5 1 V9" stroke="var(--gold)" stroke-width="0.9"/></svg>
        <span>harborlawgroup.example</span>
      </div>
      <div class="contact-address">48 Pier Lane<br>Bayport, Maine 04900</div>
    </div>
  </header>

  <div class="recipient">
    <div class="recipient-label">TO</div>
    <div class="recipient-name">Dana Whitfield</div>
    <div class="recipient-detail">Human Resources<br>Northwind Inc.<br>210 Elm Row, Suite 4<br>Springfield USA</div>
  </div>
  <div class="letter-date">Friday, 01/01/2018</div>

  <div class="letter-body">
    <p>Lorem ipsum dolor sit amet, consectetuer adipiscing elit, sed diam nonummy nibh euismod tincidunt ut laoreet dolore magna aliquam erat volutpat. Ut wisi enim ad minim veniam, quis nostrud exerci tation ullamcorper suscipit lobortis nisl ut aliquip ex ea commodo consequat. Duis autem vel eum iriure dolor in hendrerit in vulputate velit esse molestie consequat, vel illum dolore eu feugiat nulla facilisis at vero eros et accumsan et iusto odio dignissim qui blandit praesent luptatum zzril delenit augue duis dolore te feugait nulla facilisi.</p>
    <p>Nam liber tempor cum soluta nobis eleifend option congue nihil imperdiet doming id quod mazim placerat facer possim assum. Typi non habent claritatem insitam;</p>
    <p>Est usus legentis in iis qui facit eorum claritatem.</p>
    <p>Investigationes demonstraverunt lectores legere me lius quod ii legunt saepius. Claritas est etiam processus dynamicus, qui sequitur mutationem consuetudium lectorum. Mirum est notare quam littera gothica, quam nunc putamus parum claram, anteposuerit litterarum formas humanitatis per seacula quarta decima et quinta decima. Eodem modo typi, qui nunc nobis videntur parum clari, fiant sollemnes in futurum.</p>
    <p>Consectetuer adipiscing elit, sed diam nonummy nibh euismod tincidunt ut laoreet dolore magna aliquam erat volutpat. Ut wisi enim ad minim veniam, quis nostrud exerci tation ullamcorper suscipit lobortis nisl ut aliquip ex ea commodo consequat. Duis autem vel eum iriure dolor in hendrerit in vulputate velit esse molestie consequat, vel illum dolore eu feugiat nulla facilisis at vero eros et accumsan et iusto odio dignissim qui blandit praesent luptatum zzril delenit augue duis dolore te feugait nulla facilisi.</p>
    <p>Nam liber tempor cum soluta nobis eleifend option congue nihil imperdiet.</p>
  </div>

  <div class="signature">owen barrett</div>
  <div class="signer-name">Owen Barrett</div>
  <div class="signer-title">Managing Director</div>
</section>

<section class="envelope-front">
  <div class="envelope-front-band">
    <div class="brand-name">Harbor Law</div>
    <div class="return-address">48 Pier Lane<br>Bayport, Maine 04900</div>
  </div>
</section>

<section class="envelope-back">
  <div class="envelope-flap">
    <svg width="549" height="66" viewBox="0 0 549 66">
      <path d="M0 0 H549 L536 48 Q531 66 512 66 H37 Q18 66 13 48 Z" fill="var(--navy)"/>
    </svg>
    <div class="brand-name">Harbor Law</div>
  </div>
</section>

</body>
</html>
```